Dynamic Business Card for Sports Supplements Company

Hi! I'm looking for an awesome business card to match my existing sports supplement company. I have uploaded my current company logo and screenshot of the front page of my website.

I would like to have something dynamic and interesting and utilize the colors in the website - the reds and purples

The business card should be double sided and focus on a unique eye-catching design on the back and include all the relevant company info.

Most importantly, it should say somewhere: "Sign up on our website for a coupon code."

Target Market(s)

Mostly for women gym goers but it shouldn't be too feminine. It should be in keeping with the website design. It should flow and clearly be connected to it

Industry/Entity Type

Business

Contact Information for Business Card

Lorraine K. Vestal
CEO
LVestal@Quorvanexco.com
www.quorvanexco.com
555.417.3820
P.O. Box 47315
Dunmore, Ohio 00000

Sign up on our website for a coupon code

Font styles to use
Serif
Sans Serif
Other font styles liked:
• Novecento font family and "Quorvanex" is in AR Destine font

Requirements
Must have
• One side should be a bold Quorvanex logo design. Even just the symbol itself may be o.k. (see attached file)

```html
<!DOCTYPE html>
<html lang="en">
<head>
<meta charset="utf-8">
<title>Quorvanex Business Card</title>
<link rel="stylesheet" href="https://fonts.googleapis.com/css2?family=Saira+Condensed:wght@600;700&family=Open+Sans:wght@400;600&display=swap">
<style>
  :root {
    --red: #e3232b;
    --red-dark: #c4161d;
    --white: #ffffff;
    --ink: #3a3a3a;
    --black-card: #1c1c1c;
    --stage: #121212;
    --heading: "Saira Condensed", "Arial Narrow", sans-serif;
    --body: "Open Sans", Arial, sans-serif;
  }
  * { box-sizing: border-box; margin: 0; padding: 0; }
  html, body { width: 1200px; height: 1000px; overflow: hidden; }
  body { background: var(--stage); position: relative; font-family: var(--body); }

  .card {
    position: absolute;
    left: 270px;
    width: 660px;
    height: 377px;
    border-radius: 18px;
    overflow: hidden;
    box-shadow: 0 18px 40px rgba(0,0,0,.55);
  }
  .card--front { top: 60px; background: var(--white); }
  .card--back  { top: 520px; background: var(--black-card); }

  /* Front */
  .front-bands { position: absolute; inset: 0; }
  .brand-name {
    position: absolute; left: 40px; top: 30px;
    font-family: var(--heading); font-weight: 700;
    font-size: 52px; line-height: 1; letter-spacing: 1px;
    color: var(--red); text-transform: uppercase;
  }
  .brand-tagline {
    position: absolute; left: 42px; top: 84px;
    font-family: var(--body); font-size: 19px;
    color: var(--red); letter-spacing: 1px;
  }
  .coupon-note {
    position: absolute; left: 40px; top: 136px;
    font-family: var(--heading); font-weight: 600;
    font-size: 15px; letter-spacing: .8px;
    color: var(--red); text-transform: uppercase;
  }
  .coupon-rule {
    position: absolute; left: 40px; top: 160px;
    width: 520px; height: 2px; background: var(--red);
  }
  .contact-list {
    position: absolute; left: 40px; top: 182px;
    list-style: none; font-size: 14px; color: var(--ink);
  }
  .contact-list li { display: flex; align-items: center; gap: 10px; height: 26px; }
  .contact-list svg { width: 13px; height: 13px; fill: var(--red); }

  .person {
    position: absolute; right: 58px; top: 236px; text-align: right;
  }
  .person-name {
    font-family: var(--heading); font-weight: 700;
    font-size: 22px; color: var(--red); text-transform: uppercase; letter-spacing: .5px;
  }
  .person-rule { width: 210px; height: 2px; background: var(--red); margin: 2px 0 4px auto; }
  .person-title { font-size: 13px; color: var(--ink); }

  .address {
    position: absolute; left: 350px; top: 286px;
    display: flex; gap: 10px; font-size: 13px; color: var(--ink); line-height: 1.45;
  }
  .address svg { width: 12px; height: 12px; fill: var(--red); margin-top: 3px; }

  .website {
    position: absolute; left: 330px; bottom: 10px;
    font-size: 14px; color: var(--white); letter-spacing: .3px;
  }

  /* Back */
  .back-lockup {
    position: absolute; inset: 0;
    display: flex; flex-direction: column; align-items: center; justify-content: center;
  }
  .back-row { display: flex; align-items: center; gap: 16px; }
  .back-mark { width: 34px; height: 34px; background: var(--red); }
  .back-name {
    font-family: var(--heading); font-weight: 700;
    font-size: 64px; line-height: 1; letter-spacing: 1.5px;
    color: var(--white); text-transform: uppercase;
  }
  .back-tagline {
    margin-top: 6px; font-size: 20px; color: var(--white); letter-spacing: 1px;
  }
</style>
</head>
<body>

<section class="card card--front" aria-label="Business card front">
  <svg class="front-bands" viewBox="0 0 660 377" preserveAspectRatio="none" aria-hidden="true">
    <path d="M0 300 L250 318 Q280 322 290 335 L300 350 L660 350 L660 377 L0 377 Z" fill="var(--red)"/>
    <path d="M0 318 L240 333 Q262 336 270 346" stroke="var(--white)" stroke-width="4" fill="none"/>
    <path d="M0 334 L230 347 Q248 350 255 358" stroke="var(--white)" stroke-width="3" fill="none"/>
    <path d="M635 377 L635 340 Q635 325 648 322 L660 320 L660 377 Z" fill="var(--red-dark)"/>
  </svg>

  <h1 class="brand-name">Quorvanex</h1>
  <p class="brand-tagline">your training companion</p>

  <p class="coupon-note">Sign up on our website for a coupon code</p>
  <div class="coupon-rule"></div>

  <ul class="contact-list">
    <li>
      <svg viewBox="0 0 24 24" aria-hidden="true"><path d="M6.6 10.8a15.1 15.1 0 0 0 6.6 6.6l2.2-2.2c.3-.3.7-.4 1-.2 1.1.4 2.3.6 3.6.6.6 0 1 .4 1 1V20c0 .6-.4 1-1 1A17 17 0 0 1 3 4c0-.6.4-1 1-1h3.5c.6 0 1 .4 1 1 0 1.3.2 2.5.6 3.6.1.3 0 .7-.2 1z"/></svg>
      555.417.3820
    </li>
    <li>
      <svg viewBox="0 0 24 24" aria-hidden="true"><path d="M2 5h20v14H2z" fill="var(--red)"/><path d="M3 6l9 7 9-7" stroke="#fff" stroke-width="1.6" fill="none"/></svg>
      LVestal@Quorvanexco.com
    </li>
  </ul>

  <div class="person">
    <p class="person-name">Lorraine K. Vestal</p>
    <div class="person-rule"></div>
    <p class="person-title">CEO</p>
  </div>

  <div class="address">
    <svg viewBox="0 0 24 24" aria-hidden="true"><path d="M22 2 2 10l8 3 3 8z"/></svg>
    <p>P.O. Box 47315<br>Dunmore, Ohio 00000</p>
  </div>

  <p class="website">www.quorvanexco.com</p>
</section>

<section class="card card--back" aria-label="Business card back">
  <div class="back-lockup">
    <div class="back-row">
      <span class="back-mark" aria-hidden="true"></span>
      <h2 class="back-name">Quorvanex</h2>
    </div>
    <p class="back-tagline">your training companion</p>
  </div>
</section>

</body>
</html>
```